Exclusive Crestline Groomers Invite that connects barbers

I am looking for a general invitation to join a secret club of people that shave their head. I want it the size of a business card that I can hand out to people I see on the street. I want it to feel like a special exclulisve invite to a club that only they can be apart of and want to tell their friends about.

Target Market(s)

35-60 male

Industry/Entity Type

Hair

Contact Information for Business Card

I want it to look like an invite to a secret club that only people that shave their head can be apart of... I will hand it out to people that I think fir our demographic.

Font styles to use
Serif

Colors

Designer to choose colors to be used in the design.

Requirements
Must have
• A feel of exclusivity
• website address (www.crestlinegroomers.example)
• logo

```html
<!DOCTYPE html>
<html lang="en">
<head>
<meta charset="utf-8">
<title>Crestline Groomers – Invitation Card</title>
<link rel="stylesheet" href="https://fonts.googleapis.com/css2?family=Lora:wght@400;600&display=swap">
<style>
  :root {
    --backdrop: #e4e4e4;
    --card-dark-top: #383838;
    --card-dark-bottom: #242424;
    --card-light: #ffffff;
    --ink: #2b2b2b;
    --ink-soft: #555555;
    --rule: #9a9a9a;
    --icon: #8a8a8a;
    --paper: #f6f3ec;
    --accent: #c9ab6a;
  }
  * { margin: 0; padding: 0; box-sizing: border-box; }
  html, body { width: 1200px; height: 800px; overflow: hidden; }
  body {
    background: var(--backdrop);
    font-family: "Lora", serif;
    position: relative;
  }
  .card {
    position: absolute;
    top: 260px;
    width: 498px;
    height: 284px;
    border-radius: 14px;
    box-shadow: 0 10px 24px rgba(0,0,0,0.25);
    overflow: hidden;
  }
  .card--front {
    left: 88px;
    background: radial-gradient(ellipse at 50% 40%, #3e3e3e, var(--card-dark-bottom) 75%);
    color: var(--paper);
  }
  .card--back {
    left: 618px;
    background: var(--card-light);
    color: var(--ink);
  }
  .brand {
    position: absolute;
    display: flex;
    align-items: center;
    gap: 10px;
    font-weight: 600;
    white-space: nowrap;
  }
  .brand__square {
    display: block;
    border: 2px solid var(--accent);
    border-radius: 3px;
  }
  .card--front .brand {
    left: 0; right: 0; top: 150px;
    justify-content: center;
    font-size: 25px;
  }
  .card--front .brand__square { width: 20px; height: 20px; }
  .card--front .website {
    position: absolute;
    left: 0; right: 0; top: 226px;
    text-align: center;
    font-size: 13.5px;
    font-weight: 600;
    color: var(--accent);
    letter-spacing: 0.3px;
  }
  .card--back .brand {
    right: 38px; top: 97px;
    font-size: 18px;
  }
  .card--back .brand__square { width: 15px; height: 15px; }
  .holder {
    position: absolute;
    left: 35px; top: 155px;
  }
  .holder__name { font-size: 15.5px; font-weight: 600; letter-spacing: 0.3px; }
  .holder__title { font-size: 12px; color: var(--ink-soft); margin-top: 2px; letter-spacing: 0.4px; }
  .divider {
    position: absolute;
    left: 25px; right: 24px; top: 197px;
    border-top: 1px solid var(--rule);
  }
  .contact {
    position: absolute;
    font-size: 12.5px;
    line-height: 17px;
    color: var(--ink);
  }
  .contact--reach { left: 34px; top: 209px; }
  .contact--place { left: 308px; top: 212px; }
  .contact__row { display: flex; align-items: center; gap: 6px; }
  .contact__row--indent { padding-left: 18px; }
  .contact__icon { width: 12px; height: 12px; flex: none; fill: var(--icon); }
  .contact--place .contact__row { align-items: flex-start; }
  .contact--place .contact__icon { width: 12px; height: 15px; margin-top: 1px; }
</style>
</head>
<body>
  <section class="card card--front" aria-label="Card front">
    <div class="brand"><span class="brand__square"></span>Crestline Groomers</div>
    <p class="website">www.crestlinegroomers.example</p>
  </section>

  <section class="card card--back" aria-label="Card back">
    <div class="brand"><span class="brand__square"></span>Crestline Groomers</div>

    <div class="holder">
      <p class="holder__name">MAREN HALE</p>
      <p class="holder__title">MANAGING PARTNER</p>
    </div>

    <div class="divider"></div>

    <div class="contact contact--reach">
      <p class="contact__row">
        <svg class="contact__icon" viewBox="0 0 12 12" aria-hidden="true"><circle cx="6" cy="6" r="6"/><path d="M4 3.2c.4-.3.8-.2 1 .2l.4.8c.1.3 0 .5-.2.7l-.3.3c.3.7.9 1.3 1.6 1.6l.3-.3c.2-.2.5-.3.7-.2l.8.4c.4.2.5.6.2 1-.6.8-1.6.9-2.6.3C4.8 7.4 4 6.5 3.6 5.6c-.4-1-.3-1.8.4-2.4z" fill="#fff"/></svg>
        O) 555.014.2707
      </p>
      <p class="contact__row contact__row--indent">C) 555.019.8017</p>
      <p class="contact__row">
        <svg class="contact__icon" viewBox="0 0 12 12" aria-hidden="true"><circle cx="6" cy="6" r="6"/><rect x="3" y="4" width="6" height="4.2" rx=".6" fill="#fff"/><path d="M3.2 4.3 6 6.4l2.8-2.1" fill="none" stroke="#8a8a8a" stroke-width=".7"/></svg>
        mhale@crestlinegroomers.example
      </p>
    </div>

    <div class="contact contact--place">
      <p class="contact__row">
        <svg class="contact__icon" viewBox="0 0 12 15" aria-hidden="true"><path d="M6 0a5 5 0 0 0-5 5c0 3.6 5 9 5 9s5-5.4 5-9a5 5 0 0 0-5-5zm0 7a2 2 0 1 1 0-4 2 2 0 0 1 0 4z"/><rect x="1" y="14" width="10" height="1"/></svg>
        <span>410 Alder Way #200,<br>Fairmont, CO 80000</span>
      </p>
    </div>
  </section>
</body>
</html>
```